Harrow Tavern & Grille Menu Makeover

I am looking for a professional look to update our current menu. We are an independently owned sports bar and grill. Up to this point, I have done all of my own graphic designing. I am looking for something classy/family oriented. We are a very family friendly sports bar that offers a wide variety of menu options. Our website is www.harrowtavernco.example. This may help you get more of a feel for what type of place we are and what we offer. Our menu is listed on the website. My current menu is 8.5x14 inserts that feature a cover page, 4 inside pages and a back page. I would like something a little more condensed than this. Possibly a large tri-fold menu? I am open to all new ideas. I do have some pictures on my menu now, and would like to continue using a few pictures to feature some of my items. I would like something that is in a format that gives me the option to change items and prices on my own in the future. I would also like it to feature, or inform my patrons about our technology that we offer. We offer online ordering and we are a "verified venue" with Brewvoke.( a social site for craft beer lovers).

Industry/Entity Type

Sports Bar

Requirements
Nice to have
• Nice to have some pictures, but does not have to. We do feature 9 different beers on tap. A lot of them are local craft beers from the state of Kansas. Not sure if that is something we can feature, but it is a nice talking point. All of our tables and bar are hand built. With a rich mahogany finish on all of our woodwork, some type of "woodgrain" look into the menu would be nice.

```html
<!DOCTYPE html>
<html lang="en">
<head>
<meta charset="utf-8">
<title>Harrow Tavern &amp; Grille – Menu</title>
<link rel="stylesheet" href="https://fonts.googleapis.com/css2?family=Cinzel:wght@700&family=Oswald:wght@300;400&family=Michroma&display=swap">
<style>
  :root {
    --wood-dark: #4a1a0e;
    --wood-mid: #6b2b17;
    --wood-light: #8a3d22;
    --parchment-light: #e6d2a8;
    --parchment-mid: #d6bb8a;
    --parchment-edge: #a77d4a;
    --ink: #24170e;
    --ink-soft: #4b3526;
    --rule: #2e1f14;
  }
  * { margin: 0; padding: 0; box-sizing: border-box; }
  html, body { width: 850px; height: 1200px; overflow: hidden; }
  body {
    position: relative;
    background:
      repeating-linear-gradient(90deg, rgba(0,0,0,0.10) 0 2px, transparent 2px 9px, rgba(255,255,255,0.04) 9px 11px, transparent 11px 23px),
      repeating-linear-gradient(91deg, rgba(0,0,0,0.08) 0 1px, transparent 1px 37px),
      linear-gradient(90deg, var(--wood-dark), var(--wood-mid) 25%, var(--wood-light) 50%, var(--wood-mid) 75%, var(--wood-dark));
    font-family: "Oswald", sans-serif;
    color: var(--ink);
  }
  .parchment {
    position: absolute;
    left: 44px; top: 88px; width: 762px; height: 1024px;
    background:
      radial-gradient(ellipse at 50% 45%, var(--parchment-light) 0%, var(--parchment-mid) 60%, var(--parchment-edge) 100%);
    clip-path: polygon(3% 2%, 10% 1%, 18% 2.5%, 27% 1%, 36% 2%, 44% 0.5%, 53% 2%, 62% 1%, 71% 2.5%, 80% 1%, 89% 2%, 96% 1%, 99% 4%, 98% 12%, 100% 22%, 98.5% 33%, 100% 44%, 98% 55%, 99.5% 66%, 98% 77%, 100% 88%, 98% 97%, 92% 99%, 83% 97.5%, 74% 99.5%, 64% 98%, 54% 100%, 44% 98%, 34% 99.5%, 24% 97.5%, 14% 99.5%, 5% 98%, 1% 95%, 2% 85%, 0% 74%, 2% 63%, 0.5% 52%, 2% 41%, 0% 30%, 2% 19%, 0.5% 9%);
  }
  .section-title {
    position: absolute;
    left: 94px;
    font-family: "Cinzel", serif;
    font-weight: 700;
    font-size: 36px;
    letter-spacing: 0.5px;
    color: var(--ink);
  }
  .entrees-title { top: 158px; }
  .sandwiches-title { top: 587px; }
  .column { position: absolute; width: 320px; }
  .col-left { left: 98px; }
  .col-right { left: 427px; width: 345px; }
  .entrees { top: 208px; }
  .sandwiches { top: 638px; }
  .item { margin-bottom: 6px; }
  .item-beside-photo { width: 192px; }
  .item-above-photo { width: 200px; }
  .item-name {
    font-weight: 400; font-size: 15.5px; line-height: 17px;
    text-transform: uppercase; color: var(--ink);
  }
  .item-desc {
    font-weight: 300; font-size: 8.6px; line-height: 12px;
    text-transform: uppercase; color: var(--ink-soft);
  }
  .item-price {
    font-family: "Michroma", sans-serif;
    font-size: 6.5px; line-height: 9px;
    text-transform: uppercase; color: var(--ink);
  }
  .feature-photo {
    position: absolute; border-radius: 50%;
  }
  .photo-chicken {
    left: 624px; top: 134px; width: 152px; height: 152px;
    background: radial-gradient(circle at 62% 40%, #e9e2c8 0 14%, #6a4a2c 26%, #2b1a12 48%, #140d18 75%);
  }
  .photo-sandwich {
    left: 634px; top: 490px; width: 148px; height: 148px;
    background: radial-gradient(circle at 50% 55%, #d9b57a 0 18%, #8a9a3a 32%, #b84a2a 44%, #c89a66 60%, #2a1c14 85%);
  }
  .divider {
    position: absolute; left: 200px; top: 574px; width: 440px; height: 1px;
    background: var(--rule);
  }
  .divider-knot {
    position: absolute; left: 414px; top: 568px; width: 12px; height: 12px;
    border: 1.5px solid var(--rule); border-radius: 50%; background: var(--parchment-mid);
  }
  .footer {
    position: absolute; top: 1038px; left: 220px;
    display: flex; align-items: center; gap: 22px;
    font-family: "Michroma", sans-serif; font-size: 8px; letter-spacing: 0.6px;
    text-transform: uppercase; color: var(--ink);
  }
  .footer-link { display: flex; align-items: center; gap: 8px; }
  .footer-mark { width: 17px; height: 17px; background: var(--ink); }
</style>
</head>
<body>
  <div class="parchment"></div>

  <h2 class="section-title entrees-title">Entrees</h2>

  <div class="column col-left entrees">
    <div class="item"><p class="item-name">Chicken Strip Basket</p><p class="item-desc">Our classic chicken tenders served with your choice of side and dipping sauce.</p><p class="item-price">Small 5.99 / Large 8.99</p></div>
    <div class="item"><p class="item-name">Grilled Chicken Breast Fillet</p><p class="item-desc">A classic boneless, skinless chicken breast brushed with a bourbon peppercorn glaze.</p><p class="item-price">Small 7.99 / Large 10.99</p></div>
    <div class="item"><p class="item-name">Blackened Tilapia</p><p class="item-desc">8 oz. grilled tilapia filet, blackened and served with your choice of side.</p><p class="item-price">10.99</p></div>
    <div class="item"><p class="item-name">Deep Fried Catfish</p><p class="item-desc">Breaded and fried filets, served with tartar sauce.</p><p class="item-price">Small 7.99 / Large 10.99</p></div>
    <div class="item"><p class="item-name">Pepper Jack Burger Steak</p><p class="item-desc">A 12oz. ground beef patty smothered in melted pepper jack cheese and jalapeño peppers.</p><p class="item-price">Small 7.99 / Large 10.99</p></div>
    <div class="item"><p class="item-name">St. Louie Ribs</p><p class="item-desc">A three pound slab of slow roasted barbecue glazed ribs.</p><p class="item-price">Half rack 13.99 / Full rack 17.99</p></div>
    <div class="item"><p class="item-name">Pork Stuffed Baked Potato</p><p class="item-desc">Buttered and salted baked potato stuffed with a mountain of BBQ pulled pork, cheddar and jack cheese, blooming onion petals, sour cream and green onions. Served with a side salad</p><p class="item-price">8.99</p></div>
  </div>

  <div class="column col-right entrees">
    <div class="item item-beside-photo"><p class="item-name">Harrow Loaded Chicken</p><p class="item-desc">Our grilled chicken breast piled high with melted jack and cheddar cheese, sautéed onions and mushrooms, crisp bacon, and honey mustard.</p><p class="item-price">Small 9.99 / Large 12.99</p></div>
    <div class="item"><p class="item-name">Chicken Fried Chicken Dinner</p><p class="item-desc">Crispy chicken breast smothered in country gravy served with your choice of side and steamed vegetables.</p><p class="item-price">9.99</p></div>
    <div class="item"><p class="item-name">Fried Shrimp</p><p class="item-desc">A plate full of lightly breaded butterflied shrimp served with cocktail sauce.</p><p class="item-price">Small 7.99 / Large 10.99</p></div>
    <div class="item"><p class="item-name">Country Fried Steak</p><p class="item-desc">Hand breaded and deep fried, smothered in old fashioned country gravy.</p><p class="item-price">Small 7.99 / Large 10.99</p></div>
    <div class="item"><p class="item-name">Black N' Blue Sirloin</p><p class="item-desc">12 oz. choice cut sirloin cooked to your request, blackened and topped with melted blue cheese crumbles.</p><p class="item-price">15.99</p></div>
    <div class="item item-above-photo"><p class="item-name">Iron Griddle Steak</p><p class="item-desc">12 oz. aged and cut from the strip loin. Cooked to your request.</p><p class="item-price">14.99</p></div>
    <div class="item item-above-photo"><p class="item-name">Flat Iron Steak</p><p class="item-desc">9 oz. flat iron seasoned and cooked to your request.</p><p class="item-price">16.99</p></div>
  </div>

  <div class="feature-photo photo-chicken" role="img" aria-label="Photo of the loaded chicken plate with a side of dipping sauce"></div>
  <div class="feature-photo photo-sandwich" role="img" aria-label="Photo of a club sandwich with lettuce, tomato and ham"></div>

  <div class="divider"></div>
  <div class="divider-knot"></div>

  <h2 class="section-title sandwiches-title">Sandwiches</h2>

  <div class="column col-left sandwiches">
    <div class="item"><p class="item-name">Harrow Club Sandwich</p><p class="item-desc">Layers of ham, turkey, roast beef, bacon and cheese. Served with mayo on a toasted focaccia bun</p><p class="item-price">9.99</p></div>
    <div class="item"><p class="item-name">Chicken Breast Sandwich</p><p class="item-desc">Choice of crispy or grilled chicken breast, lettuce, tomato and pickles. Served with mayo on a toasted bun.</p><p class="item-price">7.99</p></div>
    <div class="item"><p class="item-name">Bang Bang Turkey Wrap</p><p class="item-desc">A grilled 12 inch tortilla stuffed with roasted turkey breast, mozzarella cheese, lettuce and our spicy bang bang sauce.</p><p class="item-price">7.99</p></div>
    <div class="item"><p class="item-name">Roast Beef &amp; Cheddar</p><p class="item-desc">Thinly sliced slow cooked roast beef smothered with a cheddar cheese sauce on a ciabatta bun. Served with spicy BBQ sauce.</p><p class="item-price">7.99</p></div>
    <div class="item"><p class="item-name">B.L.T.</p><p class="item-desc">This classic bacon, lettuce and tomato sandwich is served with mayo on your choice of white, wheat or sourdough toast.</p><p class="item-price">6.99</p></div>
    <div class="item"><p class="item-name">Hollis's Spicy Buffalo Chicken Sandwich</p><p class="item-desc">Crispy fried chicken breast smothered in Hollis's spicy buffalo sauce. Served on a ciabatta bun. Dressed with jalapeño ranch, lettuce, tomato and pickle.</p><p class="item-price">8.99</p></div>
    <div class="item"><p class="item-name">Triple Decker Reuben</p><p class="item-desc">Layer after layer of grilled corned beef, sauerkraut, swiss cheese and thousand island dressing. Served on toasted rye.</p><p class="item-price">7.99</p></div>
  </div>

  <div class="column col-right sandwiches">
    <div class="item"><p class="item-name">Classic French Dip</p><p class="item-desc">Thinly sliced roast beef grilled and loaded with swiss cheese and grilled onions. Served with french onion soup.</p><p class="item-price">8.99</p></div>
    <div class="item"><p class="item-name">Crispy Chicken Bacon Ranch Wrap</p><p class="item-desc">A 12 inch grilled tortilla stuffed with crispy chicken tenders, bacon, lettuce, tomatoes and ranch dressing.</p><p class="item-price">8.99</p></div>
    <div class="item"><p class="item-name">Southern Style Pulled Pork</p><p class="item-desc">Smoked pulled pork smothered in tangy barbecue sauce on a toasted hoagie. Served with cole slaw on request.</p><p class="item-price">7.99</p></div>
    <div class="item"><p class="item-name">Chicken Fry Steak Sandwich</p><p class="item-desc">Hand breaded chicken fried steak topped with bacon, lettuce, pickles, tomato and onion.</p><p class="item-price">7.99</p></div>
    <div class="item"><p class="item-name">Philly Steak &amp; Cheese Sandwich</p><p class="item-desc">Thinly sliced steak piled high with melted monterey jack cheese, grilled onions and peppers on a toasted hoagie.</p><p class="item-price">7.99</p></div>
    <div class="item"><p class="item-name">Eight Cheese Grilled Cheese</p><p class="item-desc">Taking this classic to the gourmet level! Eight cheeses melted thick on toasted sourdough bread.</p><p class="item-price">7.99</p></div>
    <div class="item"><p class="item-name">Chicken Cordon Bleu Sandwich</p><p class="item-desc">Your choice of crispy or grilled chicken breast layered with grilled ham, swiss cheese, lettuce, tomatoes and pickles. Served with mayo on a toasted bun.</p><p class="item-price">8.99</p></div>
  </div>

  <footer class="footer">
    <span class="footer-link"><span class="footer-mark"></span>harrowtaverngrille</span>
    <span class="footer-link"><span class="footer-mark"></span>harrowtavernco.example</span>
    <span class="footer-link"><span class="footer-mark"></span>Brewvoke</span>
  </footer>
</body>
</html>
```